Bright Harbor Design

We need a web design for our startup company based in Zurich, Switzerland called Bright Harbor. We offer professional flirt and dating advice, self development with seminars and practical coachings.

The final website aims for two capital goals. First, it will contain text, pictures and video based content presenting and advertising our services. Furthermore, we want to bind our costumers with a plattform offering them to share their expiriences related with our services.

The targeted group will be men from 25 to 40 years.
Updates

The design requires also a register-box to put in the clients Name and Email

I need (besides of the "email registration box") a "Video Gallery", "Blog" and "Agenda (with the next events to come)"

Reason: I want to make a poll now

Target Market(s)

Guys around 25 to 40 years who want to improve their social lifestyle

Industry/Entity Type

Advertising

Requirements
Must have
• First and foremost, the design must transfer strong emotions and suggest an attractive social lifestyle.

The design should not be overloaded with content but should include pictures, videos and text.

The design should present a modern, urban lifestyle.
Nice to have
• There is a logo attached to the assignement. However, if you have a good idea for an improved or different logo, please do not hesitate to design your ideas.

```html
<!DOCTYPE html>
<html lang="en">
<head>
<meta charset="utf-8">
<title>Bright Harbor – Dating &amp; Flirting Advice</title>
<link href="https://fonts.googleapis.com/css2?family=Ubuntu:ital,wght@0,400;0,500;0,700;1,400&display=swap" rel="stylesheet">
<style>
:root{
  --navy:#0d3461;
  --navy-deep:#082748;
  --orange:#f47c0e;
  --orange-light:#fba23a;
  --ink:#444;
  --muted:#666;
  --footer:#424242;
}
*{margin:0;padding:0;box-sizing:border-box}
html,body{width:1079px;height:1200px;overflow:hidden}
body{position:relative;font-family:"Ubuntu",sans-serif;color:var(--ink);background:#fff}
.abs{position:absolute}

/* header */
.site-header{left:0;top:0;width:1079px;height:106px;background:linear-gradient(#fafafa,#ececec)}
.brand{left:120px;top:34px;display:flex;align-items:center;gap:12px;font-size:30px;font-weight:500;color:var(--navy)}
.brand-dot{width:30px;height:30px;border-radius:50%;background:var(--navy)}
.main-nav{left:477px;top:60px;width:485px;height:33px;border-radius:17px;background:linear-gradient(#4a4a4a,#2f2f2f);display:flex;align-items:center;justify-content:center;font-size:12.5px;color:#fff}
.main-nav .sep{margin:0 14px;color:#ccc}

/* hero */
.hero{left:0;top:106px;width:1079px;height:400px;background:radial-gradient(circle at 50% 40%,#14457b,var(--navy-deep) 75%)}
.slider{left:117px;top:31px;width:845px;height:324px;background:#fff;box-shadow:0 10px 18px rgba(0,0,0,.45)}
.slide-photo{left:4px;top:4px;width:570px;height:315px;
  background:
    linear-gradient(90deg,rgba(255,255,255,0) 70%,#fff 100%),
    linear-gradient(180deg,rgba(60,52,46,.0) 55%,rgba(40,34,30,.55) 100%),
    linear-gradient(90deg,#3a322c 0%,#6b5e52 18%,#2b2724 30%,#8c8276 45%,#a9a49c 58%,#d6cbbd 68%,#c9c3bb 80%)}
.slide-copy{left:540px;top:56px;width:300px}
.slide-copy .lead{font-size:29px;font-weight:500;color:#555;line-height:1.1}
.slide-copy h1{font-size:31px;font-weight:500;color:var(--navy);line-height:1.2}
.slide-copy h2{font-size:18.5px;font-weight:500;color:#444;margin-top:2px}
.slide-copy p{font-size:13.5px;font-style:italic;line-height:22.5px;color:#555;margin-top:5px}
.btn{display:inline-block;background:linear-gradient(var(--orange-light),var(--orange));color:#fff;border-radius:3px;font-weight:500}
.slide-btn{left:540px;top:238px;padding:6px 10px;font-size:16px;box-shadow:0 2px 4px rgba(0,0,0,.25)}
.dots{left:738px;top:293px;display:flex;gap:5px}
.dots i{width:17px;height:17px;border-radius:50%;background:#999}
.dots i:first-child{background:#333}

/* welcome */
.couple{left:120px;top:535px;width:195px;height:195px;border-radius:50% 50% 40% 40%;background:radial-gradient(circle at 50% 45%,#b9805e 0%,#d6a789 35%,#efdcd0 60%,#fff 75%)}
.welcome{left:333px;top:538px;width:397px}
.welcome h2,.panel h2{font-weight:400;color:var(--navy)}
.welcome h2{font-size:23px}
.welcome p{font-size:11.5px;line-height:20.7px;color:var(--muted);margin-top:8px}
.read-more{left:333px;top:730px;padding:5px 8px;font-size:13.5px;background:var(--orange)}

.services{left:765px;top:541px;width:197px;height:251px;background:#efefef}
.services h3{height:29px;background:linear-gradient(#134a84,var(--navy));color:#fff;font-weight:400;font-size:18px;padding:3px 11px}
.services ul{list-style:none;padding:7px 0 0 12px}
.services li{display:flex;align-items:center;gap:14px;font-size:11.6px;color:#444;height:26px}

/* panels */
.panel{top:809px;width:270px;height:252px;background:linear-gradient(#e2e2e2,#f3f3f3 30%,#e6e6e6);border-radius:3px;box-shadow:0 8px 6px -6px rgba(0,0,0,.35)}
.panel h2{position:absolute;left:16px;top:6px;font-size:22.5px}
.thumb{position:absolute;width:109px;height:77px;background:#fff;padding:3px;box-shadow:0 1px 3px rgba(0,0,0,.3)}
.thumb div{width:100%;height:100%}
.play{position:absolute;left:50%;top:50%;transform:translate(-50%,-50%)}
.blog{position:absolute;left:16px;width:240px}
.blog .bthumb{position:absolute;left:0;top:0;width:77px;height:77px;background:#fff;padding:3px;box-shadow:0 1px 3px rgba(0,0,0,.3)}
.blog .bthumb div{width:100%;height:100%}
.blog h4{position:absolute;left:89px;top:0;font-size:13.5px;font-weight:500;color:var(--orange);white-space:nowrap}
.blog p{position:absolute;left:89px;top:17px;width:150px;font-size:11.4px;line-height:16.3px;color:#666}
.blog p em{color:var(--navy)}

/* footer */
.site-footer{left:0;top:1094px;width:1079px;height:106px;background:var(--footer)}
.foot-nav{left:117px;top:28px;font-size:11.6px;color:#eee}
.foot-nav .sep{margin:0 14px;color:#bbb}
.copy{left:117px;top:63px;font-size:10.5px;color:#aaa}
.copy b{font-weight:400;color:#fff}
.follow{left:705px;top:20px;font-size:13px;font-weight:500;color:#fff}
.social{left:703px;top:44px;display:flex;gap:9px}
.social i{width:37px;height:37px;border-radius:50%;border:2px solid #ddd;background:var(--navy)}
.social i:nth-child(2),.social i:nth-child(4){background:#2a8fcf}
.social i:nth-child(3),.social i:nth-child(6){background:#c9342a}
.social i:nth-child(5){background:#e8631a}
</style>
</head>
<body>
<svg width="0" height="0" style="position:absolute">
  <defs>
    <symbol id="heart" viewBox="0 0 12 12"><path d="M6 10.5 1.6 6A2.6 2.6 0 0 1 6 2.6 2.6 2.6 0 0 1 10.4 6z" fill="none" stroke="#f47c0e" stroke-width="1.3"/></symbol>
    <symbol id="play" viewBox="0 0 22 22"><circle cx="11" cy="11" r="10" fill="rgba(0,0,0,.7)"/><path d="M9 6.5v9l6.5-4.5z" fill="#fff"/></symbol>
  </defs>
</svg>

<header class="site-header abs">
  <div class="brand abs"><span class="brand-dot"></span>Bright Harbor</div>
  <nav class="main-nav abs">Home<span class="sep">|</span>About Us<span class="sep">|</span>Services<span class="sep">|</span>Videos<span class="sep">|</span>Gallery<span class="sep">|</span>Contact Us</nav>
</header>

<section class="hero abs">
  <div class="slider abs">
    <div class="slide-photo abs" role="img" aria-label="Photo of a smiling man and a woman flirting on a busy winter city street with trams behind them"></div>
    <div class="slide-copy abs">
      <div class="lead">Welcome to</div>
      <h1>BRIGHT HARBOR</h1>
      <h2>A Dating &amp; Flirting Advise Site...</h2>
      <p>Lorem ipsum dolor sit amet, consectetur adipi-scing elit. Fusce accumsan, elit a suscipit sag-ittis, tortor sapien cursus risus.</p>
    </div>
    <span class="btn slide-btn abs">Get Connected</span>
    <div class="dots abs"><i></i><i></i><i></i><i></i></div>
  </div>
</section>

<div class="couple abs" role="img" aria-label="Photo of a happy young couple embracing and smiling"></div>
<section class="welcome abs">
  <h2>Welcome to Our Site</h2>
  <p>Aliquam molestie, mi et imperdiet euismod, dui purus auctor tellus, et inter-dum lacus lectus et ante. Sed accumsan sollicitudin sapien, sit amet adipi-scing turpis gravida ac. In congue, neque ac lobortis volutpat, libero mauris varius mi, vitae suscipit ipsum ligula vitae risus. Duis aliquam nibh a dui iaculis viverra id a velit. Vivamus egestas risus in magna varius commodo. Sed semper viverra egestas. Etiam pretium porttitor lectus, vel ornare neque porta volutpat.</p>
</section>
<span class="btn read-more abs">Read More</span>

<aside class="services abs">
  <h3>Our Services</h3>
  <ul>
    <li><svg width="11" height="11"><use href="#heart"/></svg>Fusce accumsan</li>
    <li><svg width="11" height="11"><use href="#heart"/></svg>Phasellus dui ante</li>
    <li><svg width="11" height="11"><use href="#heart"/></svg>Morbi iaculis fringilla</li>
    <li><svg width="11" height="11"><use href="#heart"/></svg>Aliquam ullamcorper</li>
    <li><svg width="11" height="11"><use href="#heart"/></svg>Fusce accumsan</li>
    <li><svg width="11" height="11"><use href="#heart"/></svg>Phasellus dui ante</li>
    <li><svg width="11" height="11"><use href="#heart"/></svg>Morbi iaculis fringilla</li>
    <li><svg width="11" height="11"><use href="#heart"/></svg>Aliquam ullamcorper</li>
  </ul>
</aside>

<section class="panel abs" style="left:117px">
  <h2>Photo Gallery</h2>
  <div class="thumb" style="left:18px;top:45px"><div role="img" aria-label="Couple laughing close together" style="background:linear-gradient(120deg,#e6c08c,#a8683e 55%,#4a2a1a)"></div></div>
  <div class="thumb" style="left:144px;top:45px"><div role="img" aria-label="Young couple outdoors in the sun" style="background:linear-gradient(120deg,#6a3a2c,#c55a4a 45%,#d8c060)"></div></div>
  <div class="thumb" style="left:18px;top:144px"><div role="img" aria-label="Couple cheek to cheek smiling" style="background:linear-gradient(120deg,#f2d6a8,#d49a70 50%,#8a4e32)"></div></div>
  <div class="thumb" style="left:144px;top:144px"><div role="img" aria-label="Couple hugging on white background" style="background:linear-gradient(120deg,#f4f4f4,#3a2a22 50%,#e8e8e8)"></div></div>
</section>

<section class="panel abs" style="left:405px">
  <h2>Video Gallery</h2>
  <div class="thumb" style="left:18px;top:45px"><div role="img" aria-label="Video still of a couple at a night market" style="background:linear-gradient(120deg,#2a1c14,#a25a2a 50%,#d89a4a)"></div><svg class="play" width="20" height="20"><use href="#play"/></svg></div>
  <div class="thumb" style="left:144px;top:45px"><div role="img" aria-label="Video still of a couple laughing at the beach" style="background:linear-gradient(120deg,#5ec0e0,#e8d0b0 55%,#a86a44)"></div><svg class="play" width="20" height="20"><use href="#play"/></svg></div>
  <div class="thumb" style="left:18px;top:144px"><div role="img" aria-label="Video still of friends laughing at a bar" style="background:linear-gradient(120deg,#b8402a,#e8c2a8 50%,#2a3a5a)"></div><svg class="play" width="20" height="20"><use href="#play"/></svg></div>
  <div class="thumb" style="left:144px;top:144px"><div role="img" aria-label="Video still of a couple about to kiss" style="background:linear-gradient(120deg,#1e0e08,#8a3e1a 50%,#e0a050)"></div><svg class="play" width="20" height="20"><use href="#play"/></svg></div>
</section>

<section class="panel abs" style="left:693px">
  <h2>Our Blogs</h2>
  <article class="blog" style="top:45px">
    <div class="bthumb"><div role="img" aria-label="Blog photo of a smiling couple" style="background:linear-gradient(135deg,#8a6a58,#e8ddd5 55%,#7a90b0)"></div></div>
    <h4>Aliquam molestie, mi et</h4>
    <p>Sed accumsan sollicitudin sapien, sit amet adipiscing turpis gravida ac.... <em>More</em></p>
  </article>
  <div class="abs" style="left:16px;top:132px;width:240px;height:1px;background:#c9c9c9"></div>
  <article class="blog" style="top:145px">
    <div class="bthumb"><div role="img" aria-label="Blog photo of a happy couple" style="background:linear-gradient(135deg,#5a3a2a,#f0e6de 55%,#c89a80)"></div></div>
    <h4>Aliquam molestie, mi et</h4>
    <p>Sed accumsan sollicitudin sapien, sit amet adipiscing turpis gravida ac.... <em>More</em></p>
  </article>
</section>

<footer class="site-footer abs">
  <nav class="foot-nav abs">Home<span class="sep">|</span>About Us<span class="sep">|</span>Services<span class="sep">|</span>Videos<span class="sep">|</span>Gallery<span class="sep">|</span>Contact Us</nav>
  <p class="copy abs">Copyright 2013. <b>Bright Harbor.</b> All Right Reserved.</p>
  <div class="follow abs">Follow Us:</div>
  <div class="social abs" aria-label="Social links"><i></i><i></i><i></i><i></i><i></i><i></i></div>
</footer>
</body>
</html>
```